TV Antenna Installation business needs a unique flyer

We need a simple but effective flyer design for our TV Aerial installation company based in Newcastle, NSW, Australia called Bright Harbour TV & Aerial Svcs.
We are trying to target areas where there has been a new transmitter installed and most houses just require their aerial redirecting and tv's retuning.

Industry/Entity Type

Business

Requirements
Must have
• We would like the idea of a headline phrase such as " Poor TV reception……..now a thing from the past" or something similar & catchy.
Also "Did you know a new transmitter has been recently installed in your area, we can therefore now GUARANTEE 100% PERFECT PICTURE
Charges from only $95.
- Free 5 year warranty
- Free signal testing
- Free Onsite Quote
Phone 0463 527 209
Nice to have
• Other services include:

- New Installs
- Extra Points & repairs
- TV wall mounting/Home Cinema
- Pull down tall masts

Modern tv picture, see example uploaded

```html
<!DOCTYPE html>
<html lang="en">
<head>
<meta charset="utf-8">
<title>Bright Harbour TV &amp; Aerial Svcs – Flyer</title>
<link href="https://fonts.googleapis.com/css2?family=Bree+Serif&family=Open+Sans:ital,wght@0,400;0,700;1,400&display=swap" rel="stylesheet">
<style>
  :root{
    --green:#2db672;
    --orange:#f7931e;
    --white:#ffffff;
    --ink:#1c1c1c;
    --static-dark:#2a2a2a;
    --static-light:#9a9a9a;
  }
  html,body{margin:0;padding:0;overflow:hidden;}
  body{width:897px;height:1200px;background:var(--green);}
  .flyer{position:relative;width:897px;height:1200px;background:var(--green);color:var(--white);font-family:"Open Sans",sans-serif;overflow:hidden;}
  .call-block{position:absolute;left:49px;top:38px;font-family:"Bree Serif",serif;font-size:40px;line-height:50px;}
  .call-block .phone{display:flex;align-items:center;gap:8px;}
  .brand-tab{position:absolute;left:0;top:0;}
  .brand-name{position:absolute;left:410px;top:38px;font-family:"Bree Serif",serif;font-size:54px;line-height:70px;color:var(--orange);}
  .tv-visual{position:absolute;left:71px;top:170px;width:767px;height:535px;border-radius:10px 10px 40px 40px;
    background:radial-gradient(ellipse at center,var(--static-light) 0%,#6d6d6d 55%,var(--static-dark) 100%);}
  .headline{position:absolute;left:71px;top:220px;width:767px;text-align:center;font-family:"Bree Serif",serif;font-size:132px;line-height:134px;
    text-shadow:0 3px 8px rgba(0,0,0,.7);margin:0;font-weight:400;}
  .tagline{position:absolute;left:0;top:700px;width:897px;text-align:center;font-family:"Bree Serif",serif;font-size:63px;line-height:80px;margin:0;font-weight:400;}
  .offer{position:absolute;left:39px;top:790px;width:419px;height:255px;box-sizing:border-box;background:var(--orange);border:3px dashed var(--white);text-align:center;}
  .offer .price{font-family:"Bree Serif",serif;font-size:44px;line-height:54px;margin:10px 0 6px;}
  .offer ul{list-style:none;margin:0;padding:0;font-style:italic;font-size:31px;line-height:43px;}
  .intro{position:absolute;left:477px;top:788px;width:400px;font-size:24px;line-height:52px;margin:0;}
  .intro strong{font-size:30px;}
  .services-title{position:absolute;left:65px;top:1052px;font-size:35px;font-weight:700;margin:0;}
  .services{position:absolute;left:49px;top:1107px;list-style:none;margin:0;padding:0;display:grid;grid-template-columns:344px 440px;font-size:26px;line-height:38px;}
  .services li{display:flex;align-items:center;gap:6px;}
</style>
</head>
<body>
<div class="flyer">
  <svg class="brand-tab" width="897" height="142" viewBox="0 0 897 142" aria-hidden="true">
    <polygon points="323,0 897,0 897,142 387,142" fill="#ffffff"/>
  </svg>
  <div class="call-block">
    <div>Call Us Today</div>
    <div class="phone">
      <svg width="30" height="30" viewBox="0 0 30 30" aria-hidden="true"><circle cx="15" cy="15" r="13" fill="none" stroke="#fff" stroke-width="2"/><path d="M10 8c-2 2 0 8 3 11s8 5 10 3l-3-3-2 1c-2-1-4-3-5-5l1-2z" fill="#fff"/></svg>
      <span>0463 527 209</span>
    </div>
  </div>
  <div class="brand-name">Bright Harbour</div>

  <div class="tv-visual" role="img" aria-label="Flat-screen television showing grey static noise"></div>
  <h1 class="headline">Poor TV<br>signal ??</h1>

  <h2 class="tagline">NOW a thing from the past</h2>

  <div class="offer">
    <p class="price">Charges from<br>only $95</p>
    <ul>
      <li>+ Free 5 years warranty</li>
      <li>+ Free signal testing</li>
      <li>+ Free Onsite Quote</li>
    </ul>
  </div>

  <p class="intro">Did you know a new transmit-<br>ter has been recently installed<br>in your area, we can therefore<br>now <strong>GUARANTEED 100%<br>PERFECT PICTURE</strong></p>

  <h3 class="services-title">Other services include:</h3>
  <ul class="services">
    <li><svg width="22" height="18" viewBox="0 0 22 18" aria-hidden="true"><path d="M2 9l6 6L20 2" fill="none" stroke="#fff" stroke-width="3"/></svg>New Installs</li>
    <li><svg width="22" height="18" viewBox="0 0 22 18" aria-hidden="true"><path d="M2 9l6 6L20 2" fill="none" stroke="#fff" stroke-width="3"/></svg>TV wall mounting/Home Cinema</li>
    <li><svg width="22" height="18" viewBox="0 0 22 18" aria-hidden="true"><path d="M2 9l6 6L20 2" fill="none" stroke="#fff" stroke-width="3"/></svg>Extra Points &amp; repairs</li>
    <li><svg width="22" height="18" viewBox="0 0 22 18" aria-hidden="true"><path d="M2 9l6 6L20 2" fill="none" stroke="#fff" stroke-width="3"/></svg>Pull down tall masts</li>
  </ul>
</div>
</body>
</html>
```